PERI VALORE

We need a letterhead design for an Image & Etiquette Consultancy company based in Singapore.

The services we provide are Personal Image Consultation, Image & Etiquette Workshop for schools and corporate.

The design should have our corporate colour as seen in the logo files I have uploaded.

Since our company helps clients with their image, the design should be aesthetically very appealing. It should reflect a very classy & elegant feel.

I will print the letterhead using my printer but most of the time will use it to write letters to my clients therefore the format should include MS Word.

```html
<!DOCTYPE html>
<html lang="en">
<head>
<meta charset="utf-8">
<title>Peri Valore Letterhead</title>
<link rel="stylesheet" href="https://fonts.googleapis.com/css2?family=Source+Sans+3:wght@400;600&display=swap">
<style>
  :root {
    --backdrop: #e4e4e6;
    --paper: #ededf0;
    --plum: #2f0f45;
    --gold: #d9a93a;
    --ink: #1e1e22;
    --signature-ink: #8d9cc4;
    --white: #ffffff;
  }
  * { margin: 0; padding: 0; box-sizing: border-box; }
  html, body {
    width: 1113px;
    height: 1200px;
    overflow: hidden;
    background: var(--backdrop);
    font-family: "Source Sans 3", "Helvetica Neue", Arial, sans-serif;
    color: var(--ink);
  }
  .letterhead {
    position: absolute;
    left: 106px;
    top: 98px;
    width: 735px;
    height: 1039px;
    background: var(--paper);
  }
  .brand-band {
    position: absolute;
    left: 0;
    top: 50px;
    width: 377px;
    height: 80px;
    background: var(--plum);
    display: flex;
    align-items: center;
    padding-left: 32px;
  }
  .brand-name {
    font-weight: 400;
    font-size: 38px;
    letter-spacing: 2px;
    color: var(--gold);
    line-height: 1;
  }
  .greeting {
    position: absolute;
    left: 96px;
    top: 212px;
    font-size: 21px;
    font-weight: 400;
  }
  .letter-body {
    position: absolute;
    left: 96px;
    top: 280px;
    width: 543px;
    font-size: 12.6px;
    line-height: 19.8px;
    text-align: justify;
  }
  .letter-body p + p { margin-top: 19.8px; }
  .closing {
    position: absolute;
    left: 563px;
    top: 656px;
    font-size: 12.6px;
  }
  .signature {
    position: absolute;
    left: 470px;
    top: 688px;
    width: 156px;
    height: 62px;
    background: linear-gradient(180deg, rgba(141,156,196,0.15), rgba(141,156,196,0.3));
    border-radius: 4px;
  }
  .contact-band {
    position: absolute;
    left: 0;
    top: 976px;
    width: 735px;
    height: 38px;
    background: var(--plum);
    color: var(--white);
    font-size: 13.5px;
    letter-spacing: 0.3px;
  }
  .contact-band span {
    position: absolute;
    top: 10px;
    white-space: nowrap;
  }
  .contact-phone { left: 51px; }
  .contact-web { left: 291px; }
  .contact-email { right: 51px; }
</style>
</head>
<body>
  <main class="letterhead">
    <header class="brand-band">
      <span class="brand-name">PERI VALORE</span>
    </header>

    <h1 class="greeting">Dear Mr. Hale,</h1>

    <section class="letter-body">
      <p>Lorem ipsum dolor sit amet, consectetur adipiscing elit. Donec orci purus, luctus vitae dignissim eu, iaculis sed purus. Vivamus faucibus, ipsum nec aliquet viverra, leo mauris condimentum ligula, sit amet sagittis enim ligula quis arcu. Nam egestas tortor id nisi porttitor mattis. In tortor ante, ultricies in suscipit a, tempus non massa. Vivamus et auctor mi. Fusce vel massa nulla. Phasellus nec eros mauris, et scelerisque orci.</p>
      <p>Donec malesuada orci vitae nulla accumsan porta a id massa. Quisque accumsan iaculis magna sit amet fringilla. Maecenas consequat, magna eget tincidunt semper, odio nibh rutrum mi, id feugiat ante nisi eu risus. Vestibulum nunc orci, rhoncus a placerat in, ultricies in mi. Cras mattis varius eros, vel fringilla nisi suscipit eget. Quisque scelerisque sagittis nulla at porttitor.</p>
      <p>Sed id augue vitae urna euismod commodo aliquet a quam. Pellentesque arcu velit, cursus et malesuada ut, consequat et diam. Nullam erat sem, rhoncus id ullamcorper vitae, rhoncus et arcu. In ultricies ultricies nulla, ut rutrum nisi iaculis at. Donec eu magna a metus ornare faucibus. Fusce aliquet faucibus ultricies. Morbi semper, est id tincidunt gravida, sem arcu adipiscing lacus, ac bibendum nulla leo eu purus. Quisque nec diam sed risus consectetur a ccumsan quis quis nibh. Vestibulum id purus lorem.</p>
    </section>

    <p class="closing">Sincerely,</p>
    <div class="signature" role="img" aria-label="Handwritten signature of Alan Reed"></div>

    <footer class="contact-band">
      <span class="contact-phone">Tell: 555 0142</span>
      <span class="contact-web">Web: perivalore.example</span>
      <span class="contact-email">Email: hello@perivalore.example</span>
    </footer>
  </main>
</body>
</html>
```